Maple Grove Schools | brand new stationery!

We need stationery design with our new logo! Our company updated it's name and image and we like to incorporate the new one on our stationery, business cards and email signature. We are looking for fresh, new ideas!
Industry: Childcare, Elementary and Middle School
Company Name: Maple Grove Schools
Tagline: Bright Futures Start Here
Main colors: Blue, white and a little yellow
Star shape is something new for us! Do you see a way to incorporate it as a design element?

```html
<!DOCTYPE html>
<html lang="en">
<head>
<meta charset="utf-8">
<title>Maple Grove Schools – Business Card</title>
<link href="https://fonts.googleapis.com/css2?family=Montserrat:wght@400;800&family=Poppins:wght@400;600&display=swap" rel="stylesheet">
<style>
  :root{
    --page:#e6e7e9;
    --card-light:#ffffff;
    --card-dark:#231f20;
    --brand-blue:#061c72;
    --ink:#231f20;
    --muted:#3a3a3a;
    --sun:#fcc015;
  }
  *{box-sizing:border-box;margin:0;padding:0}
  html,body{width:1200px;height:393px;overflow:hidden;background:var(--page)}
  .sheet{position:relative;width:1200px;height:393px}
  .card{position:absolute;top:25px;width:569px;height:325px;overflow:hidden;
        box-shadow:0 6px 18px rgba(0,0,0,.18)}
  .card--front{left:24px;background:var(--card-light)}
  .card--back{left:609px;background:var(--card-dark)}

  .brand-disc{position:absolute;width:300px;height:300px;border-radius:50%;background:var(--brand-blue);top:40px}
  .card--front .brand-disc{left:419px}
  .card--back .brand-disc{left:-150px}

  .wordmark{position:absolute;font-family:"Poppins",sans-serif;line-height:1;text-align:center}
  .wordmark__line1{display:block;font-weight:600;letter-spacing:-.5px}
  .wordmark__line2{display:block;font-weight:400}
  .card--front .wordmark{left:40px;top:28px;width:270px;color:var(--ink)}
  .card--front .wordmark__line1{font-size:38px}
  .card--front .wordmark__line2{font-size:36px;margin-top:4px}
  .card--back .wordmark{left:185px;top:110px;width:360px;color:#fff}
  .card--back .wordmark__line1{font-size:46px}
  .card--back .wordmark__line2{font-size:48px;margin-top:6px}

  .tagline{position:absolute;left:165px;top:256px;width:380px;text-align:center;
           font-family:"Poppins",sans-serif;font-size:24px;color:var(--sun)}

  .person{position:absolute;left:53px;top:140px;font-family:"Montserrat",sans-serif}
  .person__name{font-weight:800;font-size:23px;color:var(--brand-blue);letter-spacing:-.8px;line-height:1}
  .person__role{font-size:15.5px;color:var(--muted);margin-top:4px}

  .contacts{position:absolute;left:53px;top:195px;list-style:none;font-family:"Montserrat",sans-serif;font-size:15px;color:var(--muted)}
  .contacts li{display:flex;align-items:center;height:22px}
  .contacts svg{width:14px;height:14px;margin-right:10px;fill:var(--brand-blue)}

  .address{position:absolute;left:53px;top:271px;font-family:"Montserrat",sans-serif;font-size:15px;line-height:21px;color:var(--muted);font-style:normal}
</style>
</head>
<body>
<div class="sheet">
  <section class="card card--front">
    <div class="brand-disc" role="img" aria-label="Brand star mark area"></div>
    <div class="wordmark"><span class="wordmark__line1">Maple Grove</span><span class="wordmark__line2">Schools</span></div>
    <div class="person">
      <p class="person__name">DANIEL HART</p>
      <p class="person__role">Managing Director</p>
    </div>
    <ul class="contacts">
      <li><svg viewBox="0 0 24 24"><path d="M6.6 10.8a15.1 15.1 0 0 0 6.6 6.6l2.2-2.2a1 1 0 0 1 1-.25 11.4 11.4 0 0 0 3.6.57 1 1 0 0 1 1 1V20a1 1 0 0 1-1 1A17 17 0 0 1 3 4a1 1 0 0 1 1-1h3.5a1 1 0 0 1 1 1c0 1.25.2 2.45.57 3.6a1 1 0 0 1-.25 1z"/></svg>044-555 010 246</li>
      <li><svg viewBox="0 0 24 24"><path d="M2 5h20v14H2zm2 2v.5l8 5.5 8-5.5V7l-8 5.5z"/></svg>hello@maplegrove.edu</li>
      <li><svg viewBox="0 0 24 24"><path d="M12 2a10 10 0 1 0 0 20 10 10 0 0 0 0-20zm-1 17.9A8 8 0 0 1 4.2 10.1L9 15v1a2 2 0 0 0 2 2zm6.9-2.5A2 2 0 0 0 16 16h-1v-3a1 1 0 0 0-1-1H8v-2h2a1 1 0 0 0 1-1V7h2a2 2 0 0 0 2-2v-.4a8 8 0 0 1 2.9 12.8z"/></svg>www.maplegrove.edu</li>
    </ul>
    <address class="address">18, Birchwood Lane<br>Westfield, 20714</address>
  </section>

  <section class="card card--back">
    <div class="brand-disc" role="img" aria-label="Brand star mark area"></div>
    <div class="wordmark"><span class="wordmark__line1">Maple Grove</span><span class="wordmark__line2">Schools</span></div>
    <p class="tagline">Bright Futures Start Here</p>
  </section>
</div>
</body>
</html>
```